Real Estate Company Looking for Business Card Designs for 3 Executives

Hello!
Thanks so much for considering our project! We are a real estate investment company located in Edmonton, Alberta called Bellhaven Group of Companies. We invest/develop both commercial and residential real estate and are looking to create 3 DOUBLE-SIDED business cards for 3 top executives in the company! (for some reason it won't let us select the double-sided option, but yes, the cards are double sided and would be happy to tip extra)

We have certain guidelines that we want our business cards to for sure follow - the back of the Business card has to be the Black Background Version of the Logo which has already been designed and linked as a file (first file). We want the entire back of the card to simply just be the black background logo. In terms of the front of the card, would like to see a smaller version of the white background logo (linked as the second file) in the top left hand corner - of course, feel free to get creative and we can make revisions together along the way! and Then after that, just text. We want the card to be sharp, clean, easy on the eyes and highly professional looking. We would like the card to include the Full name of the Company (Bellhaven Group of Companies), Name of the Person, Title, Phone, Email. If possible please provide the front part of the card for 3 people:

1) Bellhaven Group of Companies, Liora Quenby, Chief Financial Officer, 780-555-0142, lioraquenby@bellhavengroup.example

2) Bellhaven Group of Companies, Tobias Quenby, Chief Executive Officer, 780-555-0187, tobiasquenby@bellhavengroup.example

3) Bellhaven Group of Companies, Rui Delcourt, Chief Operations Officer, 587-555-0163, ruidelcourt@bellhavengroup.example

Thank you so much for considering our project & we look forward to seeing your designs!

```html
<!DOCTYPE html>
<html lang="en">
<head>
<meta charset="utf-8">
<title>Bellhaven Group of Companies – Business Card</title>
<link href="https://fonts.googleapis.com/css2?family=Arimo:wght@400;700&family=Montserrat:wght@700&display=swap" rel="stylesheet">
<style>
  :root {
    --backdrop: #0a0a0b;
    --card: #262628;
    --card-back: #232325;
    --ink: #ffffff;
    --ink-soft: #e6e6e8;
    --rule: #bdbdc0;
    --emboss: #3a3a3d;
  }
  * { margin: 0; padding: 0; box-sizing: border-box; }
  html, body {
    width: 1200px; height: 820px; overflow: hidden;
    background: var(--backdrop);
  }
  .canvas {
    position: relative; width: 1200px; height: 820px;
    display: flex; align-items: center; justify-content: center; gap: 60px;
  }
  .card {
    position: relative; width: 520px; height: 300px;
    background: var(--card);
    font-family: "Arimo", Arial, sans-serif;
    color: var(--ink);
  }
  .card--back { background: var(--card-back); display: flex; align-items: center; justify-content: center; }

  .brand { display: flex; align-items: center; gap: 10px; }
  .brand__square { width: 16px; height: 16px; background: var(--ink); }
  .brand__name {
    font-family: "Arimo", Arial, sans-serif; font-weight: 400;
    letter-spacing: 0.32em; color: var(--ink);
  }
  .card--front .brand { position: absolute; left: 285px; top: 62px; }
  .card--front .brand__name { font-size: 19px; }

  .card--back .brand__square { width: 26px; height: 26px; background: var(--emboss); }
  .card--back .brand__name { font-size: 30px; color: var(--emboss); }

  .rule { position: absolute; height: 1px; background: var(--rule); }
  .rule--wide { left: 40px; right: 40px; top: 150px; }
  .rule--short { left: 40px; width: 190px; top: 228px; }

  .person { position: absolute; left: 40px; top: 172px; }
  .person__name {
    font-family: "Montserrat", Arial, sans-serif; font-weight: 700;
    font-size: 20px; letter-spacing: 0.02em; text-transform: uppercase; line-height: 1.1;
  }
  .person__title { font-size: 15px; color: var(--ink-soft); margin-top: 2px; }

  .website { position: absolute; right: 40px; top: 176px; font-size: 14px; color: var(--ink-soft); }

  .contact { position: absolute; left: 44px; top: 240px; list-style: none; font-size: 15px; color: var(--ink-soft); }
  .contact li { display: flex; align-items: center; gap: 7px; line-height: 22px; }
  .contact svg { width: 14px; height: 14px; flex: none; }
</style>
</head>
<body>
<main class="canvas">
  <section class="card card--front" aria-label="Card front">
    <div class="brand">
      <span class="brand__square"></span>
      <span class="brand__name">BELLHAVEN</span>
    </div>
    <div class="rule rule--wide"></div>
    <div class="person">
      <p class="person__name">Liora Quenby</p>
      <p class="person__title">Chief Financial Officer</p>
    </div>
    <p class="website">www.bellhavengroup.example</p>
    <div class="rule rule--short"></div>
    <ul class="contact">
      <li>
        <svg viewBox="0 0 24 24" fill="none" stroke="currentColor" stroke-width="2.2" stroke-linecap="round" stroke-linejoin="round"><path d="M5 3h4l2 5-2.5 1.5a11 11 0 0 0 6 6L16 13l5 2v4a2 2 0 0 1-2 2A16 16 0 0 1 3 5a2 2 0 0 1 2-2z"/></svg>
        780-555-0142
      </li>
      <li>
        <svg viewBox="0 0 24 24" fill="none" stroke="currentColor" stroke-width="2.2" stroke-linejoin="round"><rect x="2" y="5" width="20" height="14"/><path d="M2 5l10 8 10-8"/></svg>
        lioraquenby@bellhavengroup.example
      </li>
    </ul>
  </section>

  <section class="card card--back" aria-label="Card back">
    <div class="brand">
      <span class="brand__square"></span>
      <span class="brand__name">BELLHAVEN</span>
    </div>
  </section>
</main>
</body>
</html>
```